Etiketten-Design für nachhaltige Rasur- & Pflegeprodukte
> Wir suchen Verpackung und Etiketten für eine Marke für nachhaltige Rasur- & Pflegeprodukte.
Habedere liebe Designer,
„Habedere“ sagt man bei uns in Bayern, es bedeutet Hallo oder auf Wiedersehen, je nach Gelegenheit. In diesem Fall: Hallo.
Vielleicht kennst du uns schon, wir sind greenpines, wir betreiben einen kleinen Shop für Bartpflege & Rasur unter greenpines-shop.de und wir versuchen uns nun an einem neuen Thema: nachhaltige Rasur- & Pflegeprodukte für Frauen.
Das machen wir unter dem Namen „Sanft“.
Weil die Frage schon oft aufkam: Jawohl, wir haben uns dafür die Beine und die Achseln mit einem Rasierhobel rasiert.
> Zielgruppe.
Wir arbeiten an einer neuen Pflegelinie für Frauen, die sich vorwiegend mit der Rasur und den dazugehörigen Pflegeprodukten beschäftigt. Die Zielgruppe sind vor allem online-affine Frauen aus Deutschland, Österreich und der Schweiz, aber sicher auch europaweit im Alter von 21-45.
> Aufgabenstellung.
Wir sind auf der Suche nach einem Konzept für unsere Produktverpackungen bzw. Etiketten. Bei den Pflegeprodukten verzichten wir bewusst auf eine Umverpackung.
Konkret geplant sind ein Rasierhobel, dafür haben wir eine schöne Umverpackung. Außerdem starten wir mit Rasieröl, Rasierseife und einem After Shave Balsam. Es werden später noch andere Artikel dazukommen, eine Deocreme zum Beispiel.
Rasieröl, Rasiercreme und After Shave Balsam duften nach Orangen, es werden zwei oder drei weitere Duftrichtungen folgen, die eine wird beispielsweise nach Beeren duften, die andere nach Pfirsich und Mango – bitte beachte das bei der Erstellung des Konzeptes, die Unterschiede sollten später auf den ersten Blick erkennbar sein.
Zurück zum Thema Orange: Wir würden den Duft als leicht herben Zitrusduft bezeichnen.
> Die Maße.
• Umverpackung Rasierhobel, weißer Karton (165x90x40mm)
• Rasieröl 30ml (Etikett: 100x46mm)
• Rasiercreme 60ml (Etikett: 156x32mm)
• After Shave Balsam 60ml (Etikett: 156x32mm)
> Zwingend erforderliche Angaben.
Da es sich um Kosmetikprodukte handelt, sind einige Angaben auf dem Label zwingend erforderlich, beispielhaft sollen die folgenden Infos als Platzhalter dienen.
• Hergestellt für Friedrich Lautner e.K. von greenpines, Lindenhofweg 7, 83109 Kolbermoor
• Ingredients: Aqua, Stearic Acid, Cocos Nucifera oil, Glycerin, Potassium Hydroxide, Litsea Cubeba oil, (and) Citrus Sinensis Peel oil, Orbignya Oleifera oil, Sodium Hydroxide, Macadamia ternifolia oil, Talc, Kaolin, Citric Acid, Simmondsia chinensis oil, Maris sal, C.I. 77892 (and) Rad Clay, Citral, Limonene, Linalool, Geraniol
• Platz für einen Barcode
• Rasieröl sind 30ml / 1.01 FL.OZ. ODER Creme & Balsam jeweils 60ml / 2.03 FL. OZ.
Wir haben ein Bild der aktuellen Gefäße beigefügt, es kann aber durchaus sein, dass wir uns noch umen..

```html
<!DOCTYPE html>
<html lang="de">
<head>
<meta charset="utf-8">
<title>Sanft – Etiketten Orange</title>
<link href="https://fonts.googleapis.com/css2?family=Playfair+Display:wght@400&family=Josefin+Sans:wght@700&display=swap" rel="stylesheet">
<style>
  :root {
    --stage: #e8ebe3;
    --paper: #ffffff;
    --band: #4e7670;
    --title: #4f7a70;
    --accent: #8eb5ad;
    --volume: #8aaea6;
    --ink: #1c1c1c;
    --sketch-light: #e3e7dc;
    --sketch-dark: #b9c2ab;
    --barcode: #8a8a8a;
  }
  * { margin: 0; padding: 0; box-sizing: border-box; }
  html, body { width: 1200px; height: 800px; overflow: hidden; }
  body { background: var(--stage); position: relative; font-family: "Josefin Sans", sans-serif; }

  .label { position: absolute; background: var(--paper); overflow: hidden; }
  .band { position: absolute; left: 0; right: 0; background: var(--band); }
  .band--bottom { bottom: 0; height: 12px; }
  .band--top { top: 0; height: 10px; }

  .brand { position: absolute; display: flex; align-items: center; gap: 6px;
    transform: translateX(-50%); white-space: nowrap; }
  .brand__dot { width: 9px; height: 9px; border-radius: 50%; background: var(--accent); flex: none; }
  .brand__name { font-family: "Playfair Display", serif; font-weight: 400; color: var(--title); line-height: 1; }

  .title { position: absolute; font-family: "Playfair Display", serif; font-weight: 400;
    color: var(--title); text-align: center; line-height: 1.05; transform: translateX(-50%); white-space: nowrap; }
  .volume { position: absolute; font-weight: 700; color: var(--volume); letter-spacing: 1px;
    transform: translateX(-50%); }

  .copy { position: absolute; color: var(--ink); font-weight: 700; text-transform: uppercase;
    font-size: 6.4px; line-height: 7.6px; letter-spacing: 0.1px; }
  .copy--center { text-align: center; }
  .copy--justify { text-align: justify; }
  .copy p + p { margin-top: 7px; }

  .barcode-space { position: absolute; background: var(--barcode); }
  .sketch { position: absolute; background: radial-gradient(ellipse at center, var(--sketch-dark) 0%, var(--sketch-light) 60%, rgba(255,255,255,0) 100%); }
  .vertical { position: absolute; writing-mode: vertical-rl; transform: rotate(180deg); }

  .label--long { left: 129px; width: 938px; height: 192px; }
  .label--balsam { top: 34px; }
  .label--creme { top: 247px; }
  .label--box { left: 28px; top: 486px; width: 505px; height: 275px; }
  .label--oil { left: 565px; top: 486px; width: 601px; height: 276px; }
</style>
</head>
<body>

  <section class="label label--long label--balsam">
    <div class="sketch" style="left:-20px;top:10px;width:95px;height:170px;" role="img" aria-label="Grünlich gezeichnete Orangen mit Blättern und Blüten"></div>
    <div class="brand" style="left:165px;top:28px;"><span class="brand__dot"></span><span class="brand__name" style="font-size:18px;">sanft</span></div>
    <h1 class="title" style="left:165px;top:72px;font-size:25px;">AFTER SHAVE<br>BALSAM</h1>
    <div class="volume" style="left:165px;top:151px;font-size:14px;">60ML</div>
    <div class="copy copy--center" style="left:306px;top:22px;width:218px;">Ein After Shave Balsam ist leichter verträglich als Rasierwasser und eignet sich somit für empfindliche Haut, da es weniger Alkohol enthält. Dennoch pflegt es deine Haut und beugt Irritationen sowie Reizungen vor.</div>
    <div class="sketch" style="left:343px;top:82px;width:150px;height:82px;" role="img" aria-label="Gezeichnete Orange mit Spalten und Schale"></div>
    <div class="copy copy--justify" style="left:577px;top:23px;width:223px;">
      <p>Ingredients: Aqua, Stearic Acid, Cocos Nucifera oil, Glycerin, Potassium Hydroxide, Litsea Cubeba oil, (and) Citrus Sinensis Peel oil, Orbignya Oleifera oil, Sodium Hydroxide, Macadamia Ternifolia oil, Talc, Kaolin, Citric Acid, Simmondsia Chinensis oil, Maris Sal, C.I. 77892 (and) Rad Clay, Citral, Limonene, Linalool, Geraniol</p>
      <p style="text-align:left;">Hergestellt für Friedrich Lautner e.K. von greenpines,<br>Lindenhofweg 7, 83109 Kolbermoor</p>
    </div>
    <div class="barcode-space" style="left:633px;top:110px;width:109px;height:43px;"></div>
    <div class="sketch" style="left:850px;top:15px;width:100px;height:160px;" role="img" aria-label="Gezeichneter Orangenzweig mit Blüten und Früchten"></div>
    <div class="band band--bottom"></div>
  </section>

  <section class="label label--long label--creme">
    <div class="sketch" style="left:-20px;top:10px;width:95px;height:170px;" role="img" aria-label="Grünlich gezeichnete Orangen mit Blättern und Blüten"></div>
    <div class="brand" style="left:165px;top:28px;"><span class="brand__dot"></span><span class="brand__name" style="font-size:18px;">sanft</span></div>
    <h1 class="title" style="left:165px;top:86px;font-size:25px;">RASIERCREME</h1>
    <div class="volume" style="left:165px;top:151px;font-size:14px;">60ML</div>
    <div class="copy copy--center" style="left:313px;top:22px;width:222px;">Rasiercreme ist eine weiche und praktische Alternative zu einer festen Rasierseife, die du zum Schlagen von Schaum für deine Nassrasur verwendest. Sie kann, muss aber nicht zwingend, mit einem Rasierpinsel aufgetragen werden.</div>
    <div class="sketch" style="left:345px;top:88px;width:150px;height:82px;" role="img" aria-label="Gezeichnete Orange mit Spalten und Schale"></div>
    <div class="copy copy--justify" style="left:577px;top:23px;width:223px;">
      <p>Ingredients: Aqua, Stearic Acid, Cocos Nucifera oil, Glycerin, Potassium Hydroxide, Litsea Cubeba oil, (and) Citrus Sinensis Peel oil, Orbignya Oleifera oil, Sodium Hydroxide, Macadamia Ternifolia oil, Talc, Kaolin, Citric Acid, Simmondsia Chinensis oil, Maris Sal, C.I. 77892 (and) Rad Clay, Citral, Limonene, Linalool, Geraniol</p>
      <p style="text-align:left;">Hergestellt für Friedrich Lautner e.K. von greenpines,<br>Lindenhofweg 7, 83109 Kolbermoor</p>
    </div>
    <div class="barcode-space" style="left:633px;top:111px;width:109px;height:43px;"></div>
    <div class="sketch" style="left:850px;top:15px;width:100px;height:160px;" role="img" aria-label="Gezeichneter Orangenzweig mit Blüten und Früchten"></div>
    <div class="band band--bottom"></div>
  </section>

  <section class="label label--box">
    <div class="band band--top"></div>
    <div class="brand" style="left:258px;top:46px;"><span class="brand__dot" style="width:11px;height:11px;"></span><span class="brand__name" style="font-size:24px;">sanft</span></div>
    <h1 class="title" style="left:258px;top:122px;font-size:38px;">RASIERHOBEL</h1>
    <div class="copy copy--center" style="left:130px;top:243px;width:245px;font-size:5.6px;line-height:6.8px;">Hergestellt für Friedrich Lautner e.K. von greenpines,<br>Lindenhofweg 7, 83109 Kolbermoor</div>
    <div class="band band--bottom" style="height:10px;"></div>
  </section>

  <section class="label label--oil">
    <div class="band band--top" style="height:8px;"></div>
    <div class="copy vertical" style="left:14px;top:50px;height:172px;font-size:5.4px;line-height:6.6px;">Hergestellt für Friedrich Lautner e.K. von greenpines,<br>Lindenhofweg 7, 83109 Kolbermoor</div>
    <div class="barcode-space" style="left:42px;top:83px;width:43px;height:109px;"></div>
    <div class="brand" style="left:299px;top:37px;"><span class="brand__dot"></span><span class="brand__name" style="font-size:20px;">sanft</span></div>
    <h1 class="title" style="left:299px;top:82px;font-size:34px;">RASIERÖL</h1>
    <div class="sketch" style="left:182px;top:127px;width:225px;height:96px;" role="img" aria-label="Gezeichnete Orangen, Spalten, Blätter und Blüten"></div>
    <div class="volume" style="left:299px;top:236px;font-size:17px;">30ML</div>
    <div class="copy copy--justify vertical" style="left:508px;top:22px;height:222px;font-size:5.2px;line-height:6.3px;">Um deiner Rasurvorbereitung eine neue Komponente zu verpassen eignet sich Rasieröl hervorragend. Es kann Rasurbrand, Rötungen und Hautreizungen vorbeugen, pflegt somit also deine Haut und spendet ihr zusätzlich Feuchtigkeit.</div>
    <div class="copy copy--justify vertical" style="left:552px;top:22px;height:222px;font-size:5.2px;line-height:6.3px;">Ingredients: Aqua, Stearic Acid, Cocos Nucifera oil, Glycerin, Potassium Hydroxide, Litsea Cubeba oil, (and) Citrus Sinensis Peel oil, Orbignya Oleifera oil, Sodium Hydroxide, Macadamia Ternifolia oil, Talc, Kaolin, Citric Acid, Simmondsia Chinensis oil, Maris Sal, C.I. 77892 (and) Rad Clay, Citral, Limonene, Linalool, Geraniol</div>
    <div class="band band--bottom" style="height:10px;"></div>
  </section>

</body>
</html>
```